Bluecrest Learning Corps by graduating students from college in two years

Based on the logo design, create stationary and business cards for
Dr. Venrel T Oskamp, CEO, (703) 482-1736
and Marisa Deltoft, Respresentative, (301) 647-2208
Address: 4719 Pellham Court, Faurfax Station, VA 22039
Incorporate elelments of the logo

Target Market(s)

USA

Font styles to use
Other font styles liked:
• match with the logo type style

```html
<!DOCTYPE html>
<html lang="en">
<head>
<meta charset="utf-8">
<title>Bluecrest Learning Corps – Stationery Set</title>
<link rel="stylesheet" href="https://fonts.googleapis.com/css2?family=Tinos:wght@400;700&family=Open+Sans:wght@400&family=Dancing+Script:wght@500&family=Montserrat:wght@400&display=swap">
<style>
:root{
  --navy:#1f2a63;
  --gold:#f6c431;
  --gold-deep:#e9b21c;
  --paper:#ffffff;
  --stage:#dcdddf;
  --stage-low:#d2d3d5;
  --ink:#222;
  --mute:#555;
  --ghost:#ebebee;
  --rule:#8a8a8a;
}
*{box-sizing:border-box;margin:0;padding:0}
html,body{width:1039px;height:1200px;overflow:hidden}
body{position:relative;background:var(--stage);font-family:"Tinos",serif;color:var(--ink)}
.lower-stage{position:absolute;left:0;top:826px;width:1039px;height:374px;background:linear-gradient(#e4e4e6,var(--stage-low))}
.sheet{position:absolute;background:var(--paper);box-shadow:0 2px 5px rgba(0,0,0,.18);overflow:hidden}
.rounded{border-radius:9px}

/* brand mark */
.mark{display:flex;align-items:center;justify-content:center;gap:.35em;color:var(--navy);font-family:"Tinos",serif;font-weight:700;line-height:1.05;text-align:left}
.mark-dot{flex:none;width:.9em;height:.9em;border-radius:50%;background:var(--gold)}
.mark-name{display:block}

.ghost-cap{position:absolute;background:linear-gradient(135deg,#efeff2,var(--ghost));clip-path:polygon(0 38%,58% 0,100% 38%,58% 76%)}

.person{font-weight:700;color:var(--gold)}
.role{color:var(--ink)}
.phone{display:flex;align-items:center;gap:4px;color:var(--ink)}
.phone svg,.pin svg{flex:none}
.band{position:absolute;left:0;right:0;background:var(--navy);color:#fff;display:flex;align-items:center;justify-content:center;gap:4px}

/* front business card */
.card-front{left:61px;top:79px;width:271px;height:155px}
.card-front .mark{position:absolute;left:26px;top:48px;width:80px;font-size:10px}
.card-front .divider{position:absolute;left:123px;top:37px;width:1.5px;height:81px;background:var(--gold)}
.card-front .contact{position:absolute;left:139px;top:35px;font-size:7px}
.card-front .person{font-size:12px}
.card-front .role{margin:1px 0 6px}
.card-front .phone{margin-bottom:6px}
.card-front .band{top:136px;height:9px;font-size:7px}

.card-back{left:61px;top:274px;width:271px;height:155px;display:flex;align-items:center;justify-content:center}
.card-back .mark{font-size:15px;width:150px}

/* letterhead */
.letterhead{left:348px;top:78px;width:249px;height:354px}
.letterhead .mark{position:absolute;left:22px;top:18px;width:60px;font-size:6px;justify-content:flex-start}
.letterhead .head-contact{position:absolute;left:169px;top:19px;font-size:4.3px;line-height:1.75}
.letterhead .recipient{position:absolute;left:23px;top:83px;font-family:"Open Sans",sans-serif;font-size:4.6px;line-height:1.45;color:var(--ink)}
.letterhead .recipient small{font-size:3.6px;color:var(--mute);display:block}
.letterhead .ghost-cap{left:50px;top:110px;width:160px;height:140px;opacity:.7}
.letterhead .body{position:absolute;left:23px;top:125px;width:203px;font-family:"Open Sans",sans-serif;font-size:3.9px;line-height:1.55;color:var(--mute);text-align:justify}
.letterhead .body p{margin-bottom:5px}
.letterhead .signoff{position:absolute;left:23px;top:261px;font-family:"Open Sans",sans-serif;font-size:4.3px;color:var(--mute)}
.letterhead .signoff .sig{display:block;width:32px;height:8px;margin:5px 0 4px;background:linear-gradient(90deg,#bbb,#ddd);border-radius:3px}
.letterhead .band{top:341px;height:5px;font-size:4.3px}

/* envelopes */
.env-back{left:619px;top:78px;width:357px;height:157px}
.env-back .flap{position:absolute;left:0;top:0}
.env-back .mark{position:absolute;left:138px;top:14px;width:80px;font-size:6.5px}
.env-front{left:619px;top:277px;width:357px;height:154px}
.env-front .mark{position:absolute;left:16px;top:14px;width:60px;font-size:5.5px;justify-content:flex-start}
.env-front .return{position:absolute;left:16px;top:52px;font-size:6px;line-height:1.35;color:var(--ink)}
.env-front .ghost-cap{left:114px;top:1px;width:245px;height:205px}

/* horizontal card */
.card-wide{left:60px;top:492px;width:273px;height:98px}
.card-wide .contact{position:absolute;top:31px;font-size:6.4px}
.card-wide .contact .person{font-size:10px}
.card-wide .contact .role{margin:1px 0 7px}
.card-wide .left{left:14px}
.card-wide .right{left:199px}
.card-wide .mark{position:absolute;left:117px;top:22px;width:60px;font-size:6.5px}
.card-wide .address{position:absolute;left:0;right:0;top:83px;display:flex;justify-content:center;align-items:center;gap:3px;font-size:6.4px}

/* compliments slip */
.slip{left:61px;top:637px;width:272px;height:128px}
.slip .ghost-cap{left:118px;top:30px;width:170px;height:130px}
.slip .mark{position:absolute;left:12px;top:13px;width:50px;font-size:5.5px;justify-content:flex-start}
.slip .greeting{position:absolute;left:165px;top:9px;font-family:"Dancing Script",cursive;font-size:15px;font-weight:500;color:var(--gold)}
.slip .greeting span{color:var(--navy)}
.slip .contact{position:absolute;left:13px;top:61px;font-size:4.2px;line-height:1.6}
.slip .contact .person{font-size:6.2px;line-height:1.3}
.slip .contact .pin{display:flex;gap:3px;align-items:flex-start}

/* notebook cover */
.notebook{left:365px;top:493px;width:190px;height:270px;border-radius:0 3px 3px 0;box-shadow:2px 4px 8px rgba(0,0,0,.25)}
.notebook .mark{position:absolute;left:15px;top:110px;width:160px;font-size:15px}
.spiral{position:absolute;left:357px;top:496px;width:22px;height:266px;display:flex;flex-direction:column;justify-content:space-between}
.spiral span{display:block;height:4px;border-radius:2px;background:#1c1c1c}

/* open notebook */
.journal{left:590px;top:493px;width:386px;height:271px;background:transparent;box-shadow:2px 3px 6px rgba(0,0,0,.2)}
.journal .page{position:absolute;top:0;width:193px;height:271px;background:#f7f7f8}
.journal .page.right{left:193px}
.journal .page .mark{position:absolute;left:10px;top:8px;width:40px;font-size:4.5px;justify-content:flex-start}
.journal .date{position:absolute;right:8px;top:18px;font-family:"Montserrat",sans-serif;font-size:5.5px;color:var(--mute)}
.journal .lines{position:absolute;left:9px;right:6px;top:44px;height:207px;background:repeating-linear-gradient(to bottom,transparent 0 10px,var(--rule) 10px 10.8px)}
.journal .ghost-cap{left:10px;top:80px;width:180px;height:120px;opacity:.7}
.journal .coil{position:absolute;left:186px;top:6px;width:14px;height:262px;display:flex;flex-direction:column;justify-content:space-between}
.journal .coil span{height:3px;background:#2a2a2a;border-radius:2px}

/* folders, flat */
.brochure-left{left:60px;top:872px;width:205px;height:270px}
.brochure-left .mark{position:absolute;left:22px;top:70px;width:160px;font-size:15px}
.brochure-left .foot{position:absolute;left:12px;right:12px;bottom:16px;font-size:4.3px;text-align:center;color:var(--ink);line-height:1.6}
.brochure-right{left:265px;top:872px;width:205px;height:270px;background:linear-gradient(135deg,var(--gold),#f9d35a 40%,var(--gold-deep))}
.brochure-right .mark{position:absolute;left:22px;top:80px;width:160px;font-size:15px}
.brochure-right .mark-dot{background:var(--navy)}

.folder{position:absolute;left:560px;top:872px;width:420px;height:270px;box-shadow:0 2px 6px rgba(0,0,0,.2)}
.folder .panel{position:absolute;top:0;width:210px;height:270px;background:var(--paper)}
.folder .panel.right{left:210px;border-left:1px solid #e2e2e2}
.folder .pocket{position:absolute;left:0;right:0;bottom:0;height:110px}
.folder .pocket.gold{background:var(--gold);display:flex;align-items:center;justify-content:center}
.folder .pocket.gold .mark{width:100px;font-size:8px}
.folder .pocket.navy{background:var(--navy)}
.folder .slot-card{position:absolute;left:58px;top:26px;width:96px;height:54px;background:var(--paper);padding:8px 7px;font-size:3.8px;line-height:1.5;display:flex;gap:5px}
.folder .slot-card .mark-dot{width:12px;height:12px}
.folder .slot-card .person{font-size:4.6px}
</style>
</head>
<body>

<!-- business card, front -->
<section class="sheet rounded card-front">
  <div class="mark"><span class="mark-dot"></span><span class="mark-name">Bluecrest Learning Corps</span></div>
  <div class="divider"></div>
  <div class="contact">
    <div class="person">Dr. Venrel T Oskamp</div>
    <div class="role">CEO</div>
    <div class="phone"><svg width="6" height="5" viewBox="0 0 12 10"><path d="M1 4c0-3 10-3 10 0l-2 1-1-1H4L3 5z M3 5h6l1 5H2z" fill="#f6c431"/></svg>(703) 482-1736</div>
    <div class="person">Marisa Deltoft</div>
    <div class="role">Respresentative</div>
    <div class="phone"><svg width="6" height="5" viewBox="0 0 12 10"><path d="M1 4c0-3 10-3 10 0l-2 1-1-1H4L3 5z M3 5h6l1 5H2z" fill="#f6c431"/></svg>(301) 647-2208</div>
  </div>
  <div class="band"><svg width="5" height="6" viewBox="0 0 10 12"><path d="M5 0a4 4 0 0 1 4 4c0 3-4 8-4 8S1 7 1 4a4 4 0 0 1 4-4z" fill="#fff"/><circle cx="5" cy="4" r="1.5" fill="#1f2a63"/></svg>4719 Pellham Court, Faurfax Station, VA 22039</div>
</section>

<!-- business card, back -->
<section class="sheet rounded card-back">
  <div class="mark"><span class="mark-dot"></span><span class="mark-name">Bluecrest Learning Corps</span></div>
</section>

<!-- letterhead -->
<section class="sheet letterhead">
  <div class="mark"><span class="mark-dot"></span><span class="mark-name">Bluecrest Learning Corps</span></div>
  <div class="head-contact">
    <div>Dr. Venrel T Oskamp, CEO</div>
    <div><span style="color:var(--gold)">☎</span> (703) 482-1736</div>
    <div>Marisa Deltoft, Respresentative</div>
    <div><span style="color:var(--gold)">☎</span> (301) 647-2208</div>
  </div>
  <div class="recipient">ORLA PENHALIGON<small>Chief Exective Officer</small><small>City/State, Zip Code</small></div>
  <div class="ghost-cap" role="img" aria-label="Faint watermark of the brand symbol"></div>
  <div class="body">
    <p>Thank you for your interest in our accelerated two-year degree pathway. Our cohorts pair focused coursework in science, technology, engineering and math with mentoring and paid lab placements, so students graduate ready for the workforce.</p>
    <p>This letter confirms your enrollment review for the coming term. Please bring transcripts and a photo ID to orientation, where advisors will build your semester plan and match you with a faculty mentor.</p>
    <p>We look forward to welcoming you and supporting every step toward your degree.</p>
  </div>
  <div class="signoff">Sincerely,<span class="sig" role="img" aria-label="Handwritten signature"></span>Corin Ashby</div>
  <div class="band">⌖ 4719 Pellham Court, Faurfax Station, VA 22039</div>
</section>

<!-- envelope, back -->
<section class="sheet env-back">
  <svg class="flap" width="357" height="157" viewBox="0 0 357 157"><path d="M2 2 Q10 40 20 52 Q30 57 45 57 H330 Q345 56 352 45 L356 30" fill="none" stroke="#d8d8d8" stroke-width="1"/></svg>
  <div class="mark"><span class="mark-dot"></span><span class="mark-name">Bluecrest Learning Corps</span></div>
</section>

<!-- envelope, front -->
<section class="sheet env-front">
  <div class="ghost-cap" role="img" aria-label="Faint watermark of the brand symbol"></div>
  <div class="mark"><span class="mark-dot"></span><span class="mark-name">Bluecrest Learning Corps</span></div>
  <div class="return">4719 Pellham Court,<br>Faurfax Station, VA 22039</div>
</section>

<!-- business card, horizontal -->
<section class="sheet card-wide">
  <div class="contact left">
    <div class="person">Dr. Venrel T Oskamp</div>
    <div class="role">CEO</div>
    <div class="phone"><span style="color:var(--gold)">☎</span>(703) 482-1736</div>
  </div>
  <div class="mark"><span class="mark-dot"></span><span class="mark-name">Bluecrest Learning Corps</span></div>
  <div class="contact right">
    <div class="person">Marisa Deltoft</div>
    <div class="role">Respresentative</div>
    <div class="phone"><span style="color:var(--gold)">☎</span>(301) 647-2208</div>
  </div>
  <div class="address"><svg width="5" height="6" viewBox="0 0 10 12"><path d="M5 0a4 4 0 0 1 4 4c0 3-4 8-4 8S1 7 1 4a4 4 0 0 1 4-4z" fill="#f6c431"/><circle cx="5" cy="4" r="1.5" fill="#fff"/></svg>4719 Pellham Court, Faurfax Station, VA 22039</div>
</section>

<!-- compliments slip -->
<section class="sheet slip">
  <div class="ghost-cap" role="img" aria-label="Faint watermark of the brand symbol"></div>
  <div class="mark"><span class="mark-dot"></span><span class="mark-name">Bluecrest Learning Corps</span></div>
  <div class="greeting"><span>with</span> compliments</div>
  <div class="contact">
    <div class="person">Dr. Venrel T Oskamp</div>
    <div>CEO</div>
    <div><span style="color:var(--gold)">☎</span> (703) 482-1736</div>
    <div class="pin"><span style="color:var(--gold)">⌖</span><span>4719 Pellham Court,<br>Faurfax Station, VA 22039</span></div>
    <div class="person">Marisa Deltoft</div>
    <div>Respresentative</div>
    <div><span style="color:var(--gold)">☎</span> (301) 647-2208</div>
  </div>
</section>

<!-- notebook cover -->
<section class="sheet notebook">
  <div class="mark"><span class="mark-dot"></span><span class="mark-name">Bluecrest Learning Corps</span></div>
</section>
<div class="spiral"><span></span><span></span><span></span><span></span><span></span><span></span><span></span><span></span><span></span><span></span><span></span><span></span><span></span><span></span><span></span><span></span><span></span></div>

<!-- open notebook -->
<section class="sheet journal">
  <div class="page left">
    <div class="ghost-cap" role="img" aria-label="Faint watermark of the brand symbol"></div>
    <div class="mark"><span class="mark-dot"></span><span class="mark-name">Bluecrest Learning Corps</span></div>
    <div class="date">Date......./....../.......</div>
    <div class="lines"></div>
  </div>
  <div class="page right">
    <div class="ghost-cap" role="img" aria-label="Faint watermark of the brand symbol"></div>
    <div class="mark"><span class="mark-dot"></span><span class="mark-name">Bluecrest Learning Corps</span></div>
    <div class="date">Date......./....../.......</div>
    <div class="lines"></div>
  </div>
  <div class="coil"><span></span><span></span><span></span><span></span><span></span><span></span><span></span><span></span><span></span><span></span><span></span><span></span><span></span><span></span><span></span><span></span><span></span><span></span><span></span><span></span><span></span><span></span><span></span><span></span><span></span></div>
</section>

<div class="lower-stage"></div>

<!-- presentation folder, outside -->
<section class="sheet brochure-left">
  <div class="mark"><span class="mark-dot"></span><span class="mark-name">Bluecrest Learning Corps</span></div>
  <div class="foot">Dr. Venrel T Oskamp, CEO · (703) 482-1736 · Marisa Deltoft, Respresentative · (301) 647-2208<br>4719 Pellham Court, Faurfax Station, VA 22039</div>
</section>
<section class="sheet brochure-right">
  <div class="mark"><span class="mark-dot"></span><span class="mark-name">Bluecrest Learning Corps</span></div>
</section>

<!-- presentation folder, inside -->
<section class="folder">
  <div class="panel left">
    <div class="pocket gold"><div class="mark"><span class="mark-dot" style="background:var(--navy)"></span><span class="mark-name">Bluecrest Learning Corps</span></div></div>
  </div>
  <div class="panel right">
    <div class="pocket navy">
      <div class="slot-card">
        <span class="mark-dot"></span>
        <div>
          <div class="person">Dr. Venrel T Oskamp</div>
          <div>CEO</div>
          <div>4719 Pellham Court,<br>Faurfax Station, VA 22039</div>
          <div>(703) 482-1736</div>
        </div>
      </div>
    </div>
  </div>
</section>

</body>
</html>
```